Mobile Friendly Lead Generation Landing Page

We are a web marketing company that specialized in web lead generation. Recently we have started buying media from mobile devices and we need a mobile interface(landing page) where we can collect user data in an effective manner.

Our current mobile landing page is:
http://www.tutorpath.example.com/lp13d/index.aspx?a=true&source=841356
Through this you can see what the steps/questions users need to answer to get matched to a school. We need the design for the whole process.

We are pretty open for design ideas and our goal is to make this mobile optimized landing page have the look and feel of an app...but not an app.
There are several questions in the process but we are open to changing the way they are presented. As in, you can have one question at a time or a few.
The goal is to make this EXTREMELY EASY for users to interact with.

One example that we have liked is:
http://learnvane.example/schools/57214-page1.lvne (please note that this opens only on mobile devices)

Some of these screenshots are attached.

Our web form looks like this:
http://www.tutorpath.example.com/lp88/index.aspx?a=true

```html
<!DOCTYPE html>
<html lang="en">
<head>
<meta charset="utf-8">
<title>TutorPath – School Match Form</title>
<link rel="stylesheet" href="https://fonts.googleapis.com/css2?family=Open+Sans:wght@300;400;700&display=swap">
<style>
  :root {
    --header-bg: #3e5064;
    --progress-bg: #26313f;
    --track: #3a4b5e;
    --track-empty: #4a5b6e;
    --fill-dark: #3a9a1e;
    --fill-light: #7cc24f;
    --progress-text: #7d8998;
    --page-bg: #e9e9e9;
    --card-bg: #ffffff;
    --card-shadow: rgba(0,0,0,0.12);
    --question-text: #6d6d6d;
    --option-circle: #ececec;
    --option-ring: #d7d7d7;
    --tick: #6cbf3a;
    --cross: #ee5a5a;
    --brand-text: #7f8a2a;
    --badge-red: #c8102e;
    --badge-blue: #1e4e72;
    --white: #ffffff;
  }
  * { box-sizing: border-box; margin: 0; padding: 0; }
  html, body { width: 725px; height: 1200px; overflow: hidden; }
  body { font-family: "Open Sans", Arial, sans-serif; background: var(--page-bg); }
  .screen { position: relative; width: 725px; height: 1200px; background: var(--page-bg); overflow: hidden; }

  .title-bar {
    position: absolute; left: 0; top: 0; width: 725px; height: 106px;
    background: var(--header-bg);
    display: flex; align-items: center; justify-content: center;
    color: var(--white); font-size: 25px; font-weight: 400;
  }
  .title-bar strong { font-weight: 700; margin: 0 7px; }
  .nav-arrow { position: absolute; top: 35px; width: 36px; height: 36px; }
  .nav-arrow.back { left: 50px; }
  .nav-arrow.next { right: 26px; }

  .progress-panel {
    position: absolute; left: 0; top: 106px; width: 725px; height: 198px;
    background: var(--progress-bg);
  }
  .progress-step { position: absolute; top: 66px; height: 37px; border-radius: 3px; background: var(--track); overflow: hidden; }
  .progress-step.one { left: 90px; width: 118px; }
  .progress-step.two { left: 219px; width: 264px; }
  .progress-step.three { left: 492px; width: 155px; background: var(--track-empty); }
  .progress-fill { height: 100%; background: repeating-linear-gradient(135deg, rgba(255,255,255,0.08) 0 3px, transparent 3px 6px), var(--fill-dark); }
  .progress-fill.partial { width: 95px; background: repeating-linear-gradient(135deg, rgba(255,255,255,0.1) 0 3px, transparent 3px 6px), var(--fill-light); }
  .progress-label {
    position: absolute; top: 122px; width: 100%; text-align: center;
    font-size: 15px; color: var(--progress-text);
  }

  .question-card {
    position: absolute; left: 28px; top: 339px; width: 671px; height: 600px;
    background: var(--card-bg); border-radius: 4px;
    box-shadow: 0 2px 3px var(--card-shadow);
  }
  .question-title {
    margin-top: 44px; text-align: center;
    font-size: 34px; font-weight: 300; color: var(--question-text);
  }
  .answer-list { list-style: none; position: absolute; left: 237px; top: 196px; }
  .answer { display: flex; align-items: center; height: 60px; margin-bottom: 68px; font-size: 34px; font-weight: 300; color: var(--question-text); }
  .answer-icon { width: 60px; height: 60px; margin-right: 36px; }

  .trust-strip {
    position: absolute; left: 28px; top: 975px; width: 671px; height: 150px;
    background: var(--card-bg); border-radius: 4px;
    box-shadow: 0 2px 3px var(--card-shadow);
  }
  .brand-name {
    position: absolute; left: 42px; top: 56px;
    font-size: 28px; font-weight: 700; color: var(--brand-text);
  }
  .badge { position: absolute; }
  .badge.security { left: 285px; top: 42px; width: 120px; height: 66px; background: var(--badge-red); border-radius: 6px; }
  .badge.rating { left: 520px; top: 50px; width: 104px; height: 52px; background: var(--badge-blue); border-radius: 4px; }
</style>
</head>
<body>
<main class="screen">
  <header class="title-bar">
    <svg class="nav-arrow back" viewBox="0 0 36 36" aria-label="Back">
      <circle cx="18" cy="18" r="16" fill="none" stroke="#9aa7b6" stroke-width="2"/>
      <path d="M25 18H11M17 12l-6 6 6 6" fill="none" stroke="#9aa7b6" stroke-width="2" stroke-linecap="round" stroke-linejoin="round"/>
    </svg>
    Fill out our <strong>2 MINUTE</strong> form!
    <svg class="nav-arrow next" viewBox="0 0 36 36" aria-label="Next">
      <circle cx="18" cy="18" r="16" fill="none" stroke="#9aa7b6" stroke-width="2"/>
      <path d="M11 18h14M19 12l6 6-6 6" fill="none" stroke="#9aa7b6" stroke-width="2" stroke-linecap="round" stroke-linejoin="round"/>
    </svg>
  </header>

  <section class="progress-panel">
    <div class="progress-step one"><div class="progress-fill"></div></div>
    <div class="progress-step two"><div class="progress-fill partial"></div></div>
    <div class="progress-step three"></div>
    <p class="progress-label">progress : 76% completed</p>
  </section>

  <section class="question-card">
    <h1 class="question-title">Are you currently in school?</h1>
    <ul class="answer-list">
      <li class="answer">
        <svg class="answer-icon" viewBox="0 0 60 60" aria-hidden="true">
          <circle cx="30" cy="30" r="29" fill="var(--option-circle)" stroke="var(--option-ring)"/>
          <path d="M19 31l8 8 15-17" fill="none" stroke="var(--tick)" stroke-width="5" stroke-linecap="round" stroke-linejoin="round"/>
        </svg>
        Yes
      </li>
      <li class="answer">
        <svg class="answer-icon" viewBox="0 0 60 60" aria-hidden="true">
          <circle cx="30" cy="30" r="29" fill="var(--option-circle)" stroke="var(--option-ring)"/>
          <path d="M21 21l18 18M39 21L21 39" fill="none" stroke="var(--cross)" stroke-width="5" stroke-linecap="round"/>
        </svg>
        No
      </li>
    </ul>
  </section>

  <footer class="trust-strip">
    <span class="brand-name">TutorPath</span>
    <div class="badge security" role="img" aria-label="Security certification badge"></div>
    <div class="badge rating" role="img" aria-label="Business rating badge"></div>
  </footer>
</main>
</body>
</html>
```